Website development company website

ABOUT COMPANY
Hi everyone! We're a Melbourne, Australia website development company in a need of a website design that will make online store merchants want to engage our services.
We specialise exclusively in Torvista e-commerce platform (https://torvista-platform.example/). What distinguishes our business from competition is that rather than designing and building brand new websites, we offer development, support and maintenance services to established websites. Maintenance and Support are the keywords representing our business.
Our potential clients are people with broken, slow and underperforming Torvista installations who need assistance getting their websites up and making sales. Our website must pass the message that we can help, and provide quick means of making contact.
DESIGN
Overall, we're looking for a slick, clean, airy, conservative design. No need to do anything crazy, try to stick to what's "standard" in website design these days and make it easy on all of us. The website is unlikely to be updated too often so it needs to look attractive and fresh first time over and after a year, too.
Attached is our new logo, which you'll be able to take the basic idea from, the colors and fonts. Though, don't use the fonts from the logo in the website, stick to the standard widely supported fonts. Additional use of Google fonts is fine.
Don't overdo it with colors, stick to conservative basic color set and only use the colors from the log for accents like headings etc. Please, don't be tempted to use the blue and orange as background of whole blocks, other than perhaps footer. Thanks.
For the images used, I'd like to stay away from a design studio/digital agency feel and lean more towards professional support and maintenance services. I'm thinking images of content merchants doing their job. Something along the lines of "We'll be taking care of the website so that you only need to care about the business".
Some ideas I like:
http://www.plumframe-pics.example/detail/photo/portrait-of-confident-male-design-professional-royalty-free-image/572048163
http://www.plumframe-pics.example/detail/photo/designer-taking-picture-of-hat-high-res-stock-photography/839207514
http://www.plumframe-pics.example/detail/photo/woman-packaging-pottery-royalty-free-image/216684093
Images of colorful shopping bags and shopping carts are over the top and not serious enough. Instead of images matching Online Shopping, I'd try going more for Stability, Reliability, Performance.
Our existing website is http://www.bravuln.example. Please, don't take design ideas from it, but it will give you a picture of the structure of our new website and content that's going to be used initially.
If you could include a basic icon set to use throughout the website, that would be great. If the icons could match our logo (attached), it would be a big plus.
ALL PAGES
Every page must contain clearly visible phone number (1300 648 907) and a Contact Us Now button, which opens an AJAX driven popup form with Name, Email, Phone and Message to be sent through.
To start with, main menu items will be Torvista, Portfolio, Contact.
At the bottom of each page, please, include a newsletter subscription form with text Subscribe to Torvista Support and Security Updates.
For the footer, I'd like to see a logo strip with the following logos in grayscale (no need to link anywhere): Torvista, QRX, DataVane, NCB. You'll find the logos on Google Images.
Standard footer columns follow. Here, I'd like to see logos in color: Torvista Certified Developer, Torvista Ceritified Solution Provider. Again, the logos are on Google Images.
No social media logos/links necessary anywhere on the website.
...and then the copyright line.
FRONT PAGE
Large slider with images that would appeal to our target audience. Keywords here would be Torvista System Audit, Torvista Performance Optimisation, Torvista Website Emergency Recovery, Torvista Development Infrastructure Hosting. We'll have a static page created for each of these to link to.
In a corner of the slider, or on the edge, can I have an overlay with logos in color (same as footer): Torvista Certified Developer, Torvista Ceritified Solution Provider.
Underneath, a number of blocks, each with an image and teaser that we'll use to link to various pages throughout the website.
PORTFOLIO PAGE
I'm thinking a single long page with a block per client, which will contain project name, description from us and a testimonial from client. Also, each block will contain a single large screenshot. No gallery or slideshow is necessary here, just one image per project.
I'll leave the layout up to you, but try to put yourself in the shoes of a potential client reviewing our past work by simply scrolling down this one page.
CONTACT US PAGE
Separate page with the same form as above, phone number (1300 648 907), email address (support@kavreo.example), address (Suite 42, Level 3|8 Wattlebrook Lane|Fernvale Heights VIC 3999), and a grayscale Google Map.
CODING UP
Coding up into static HTML/CSS/JS is equally important as the design itself. We're a website development company, we'll be integrating the theme. We will spot any issues and we will point them out.
Coded up design must be fully responsive. Enough said.
To be able to create any content in future, we'd like one extra page coded up with samples of all themed elements, lists, forms, buttons, 2, 3, 4-column layout, alerts, icons, etc. This page does not need to be designed, only coded up.
The design will be integrated into Drupal using Twig. If possible at all, try to keep it in mind when designing and coding up, and make the integration into a Drupal theme easier for us.
GOOD LUCK!
That's it. Let me know if anything needs clarifying. So far I've had a great experience with ArtFlockly. I don't doubt some great designs will emerge. Clever ideas are highly appreciated, but also make it clear you've read and followed the points in this brief. Cheers, Tom

```html
<!DOCTYPE html>
<html lang="en">
<head>
<meta charset="utf-8">
<title>Contact – Kavreo</title>
<link href="https://fonts.googleapis.com/css2?family=Open+Sans:wght@400;600;700&family=Roboto+Condensed:wght@400;700&display=swap" rel="stylesheet">
<style>
:root{
  --navy:#0d3a6b;
  --orange:#ee7d22;
  --orange-light:#f39148;
  --text:#444;
  --muted:#666;
  --line:#ddd;
  --field:#f6f6f6;
  --strip:#f1f1f1;
  --footer:#2b2b2b;
  --footer-text:#9a9a9a;
  --bottom:#161616;
}
*{box-sizing:border-box;margin:0;padding:0}
html,body{width:998px;height:1200px;overflow:hidden}
body{font-family:"Open Sans",Arial,sans-serif;color:var(--text);background:#fff;position:relative}
.wrap{position:absolute;left:134px;width:730px}

.topbar{position:absolute;top:0;left:0;width:998px;height:24px;background:var(--navy)}
.topbar .phone{position:absolute;left:134px;top:2px;height:19px;padding:0 6px 0 2px;border:1px solid #fff;border-radius:4px;color:#fff;font:400 11px "Roboto Condensed",sans-serif;display:flex;align-items:center;gap:5px}
.topbar .phone .dot{width:15px;height:15px;border-radius:50%;background:#fff;display:flex;align-items:center;justify-content:center}
.topbar .cta{position:absolute;right:134px;top:3px;height:18px;background:var(--orange);color:#fff;border-radius:3px;font:400 11px "Roboto Condensed",sans-serif;display:flex;align-items:center;padding:0 5px;gap:6px}
.topbar .cta .sep{width:1px;height:12px;background:#fff}

.header{position:absolute;top:24px;left:0;width:998px;height:52px;background:#fff}
.brand{position:absolute;left:134px;top:12px;display:flex;align-items:center;gap:6px;font-weight:700;font-size:21px;color:var(--orange)}
.brand .mark{width:22px;height:26px;background:var(--navy);border-radius:2px}
.nav{position:absolute;right:134px;top:22px;display:flex;gap:20px;font-size:9.5px;color:#333}
.nav .active{border-bottom:2px solid var(--orange);padding-bottom:8px}

.banner{position:absolute;top:76px;left:0;width:998px;height:65px;background:linear-gradient(90deg,#ec6a1e,#f39148 50%,#ec6a1e)}
.banner h1{position:absolute;left:134px;top:23px;font-weight:400;font-size:19px;color:#fff;letter-spacing:.5px}
.crumbs{position:absolute;right:134px;top:29px;font-size:9.5px;color:#fff}

h2.section{font-size:11.5px;font-weight:600;color:#333;position:relative;padding-bottom:8px}
h2.section::after{content:"";position:absolute;left:0;bottom:0;width:23px;height:2px;background:#999}

.form-col{position:absolute;left:134px;top:159px;width:418px}
.field{position:absolute;left:0;width:418px;font-size:9px;color:#555}
.field label{position:absolute;left:0;top:8px}
.field label b{color:#e22;font-weight:400}
.field .input{position:absolute;left:62px;top:0;width:356px;height:26px;border:1px solid var(--line);border-radius:3px;background:var(--field)}
.btn{position:absolute;left:62px;top:231px;width:95px;height:28px;background:var(--orange);color:#fff;font-size:9px;display:flex;align-items:center;justify-content:center;border-radius:2px}

.info-col{position:absolute;left:571px;top:159px;width:293px}
.info{position:absolute;left:0;display:flex;gap:11px}
.info .icon{width:44px;height:41px;background:var(--orange);border-radius:2px;display:flex;align-items:center;justify-content:center;flex:none}
.info h3{font-size:9px;font-weight:700;color:#333;margin:0 0 6px}
.info p{font-size:9.5px;line-height:12.5px;color:#444}

.map{position:absolute;top:451px;left:0;width:998px;height:331px;background:linear-gradient(135deg,#e4e4e4,#d8d8d8 55%,#e2e2e2)}

.tech-strip{position:absolute;top:806px;left:0;width:998px;height:120px;background:linear-gradient(#f7f7f7,var(--strip))}
.tech-strip ul{list-style:none;position:absolute;left:134px;width:730px;top:0;height:120px;display:flex;justify-content:space-around;align-items:center}
.tech-strip li{font-size:26px;font-weight:600;color:#555;letter-spacing:-.5px;display:flex;align-items:center;gap:8px}
.tech-strip li .sq{width:22px;height:22px;background:#777}

.footer{position:absolute;top:958px;left:0;width:998px;height:206px;background:var(--footer);color:var(--footer-text);font-size:8.8px;line-height:12.5px}
.footer .col{position:absolute;top:14px}
.footer h4{font-size:10.5px;font-weight:600;color:#bbb;position:relative;padding-bottom:5px;margin-bottom:14px}
.footer h4::after{content:"";position:absolute;left:0;bottom:0;width:18px;height:1px;background:#888}
.about{left:134px;width:224px;text-align:justify}
.badges{display:flex;gap:14px;margin-top:9px}
.badge{width:36px;height:66px;background:#e8e8e8;border-radius:3px 3px 0 0}
.badge.orange{background:var(--orange)}
.address-col{left:384px;width:200px}
.address-col h4.sub{margin-top:6px;margin-bottom:9px}
.contact-line{display:flex;align-items:center;gap:6px;font-size:9px}
.contact-line .dot{width:18px;height:18px;border-radius:50%;background:#555;display:flex;align-items:center;justify-content:center}
.news-col{left:634px;width:230px}
.news-col .email{margin-top:19px;width:187px;height:25px;background:#6a6a6a;border-radius:2px;color:#ddd;padding:6px 7px;font-size:8.5px}
.news-col .sub-btn{margin-top:14px;width:64px;height:24px;background:var(--orange);color:#fff;display:flex;align-items:center;justify-content:center;font-size:8.5px;border-radius:2px}

.bottombar{position:absolute;top:1164px;left:0;width:998px;height:36px;background:var(--bottom);font-size:8.5px;color:#999}
.bottombar nav{position:absolute;left:134px;top:13px;display:flex;gap:15px}
.bottombar .copy{position:absolute;right:134px;top:13px}
</style>
</head>
<body>

<div class="topbar">
  <div class="phone"><span class="dot"><svg width="9" height="9" viewBox="0 0 24 24"><path fill="#ee7d22" d="M6.6 10.8a15 15 0 0 0 6.6 6.6l2.2-2.2c.3-.3.7-.4 1-.2 1.1.4 2.3.6 3.6.6.6 0 1 .4 1 1V20c0 .6-.4 1-1 1A17 17 0 0 1 3 4c0-.6.4-1 1-1h3.5c.6 0 1 .4 1 1 0 1.3.2 2.5.6 3.6.1.3 0 .7-.2 1z"/></svg></span>1300 648 907</div>
  <div class="cta">Contact Us Now<span class="sep"></span><svg width="10" height="10" viewBox="0 0 24 24"><circle cx="12" cy="12" r="11" fill="#fff"/><path d="M10 7l5 5-5 5" stroke="#ee7d22" stroke-width="3" fill="none"/></svg></div>
</div>

<header class="header">
  <div class="brand"><span class="mark"></span>Kavreo</div>
  <nav class="nav"><span>HOME</span><span>TORVISTA</span><span>PORTFOLIO</span><span class="active">CONTACT</span></nav>
</header>

<section class="banner">
  <h1>CONTACT</h1>
  <div class="crumbs">HOME &nbsp;»&nbsp; CONTACT</div>
</section>

<section class="form-col">
  <h2 class="section">LEAVE A MESSAGE</h2>
  <div class="field" style="top:31px"><label>NAME<b>*</b>:</label><div class="input"></div></div>
  <div class="field" style="top:67px"><label>EMAIL<b>*</b>:</label><div class="input"></div></div>
  <div class="field" style="top:103px"><label>PHONE<b>*</b>:</label><div class="input"></div></div>
  <div class="field" style="top:139px"><label>MESSAGE<b>*</b>:</label><div class="input" style="height:82px"></div></div>
  <div class="btn">SEND MESSAGE</div>
</section>

<section class="info-col">
  <h2 class="section">GET IN TOUCH</h2>
  <div class="info" style="top:31px">
    <div class="icon"><svg width="14" height="18" viewBox="0 0 24 32"><path fill="#fff" d="M12 0a11 11 0 0 0-11 11c0 8 11 21 11 21s11-13 11-21A11 11 0 0 0 12 0zm0 15a4 4 0 1 1 0-8 4 4 0 0 1 0 8z"/></svg></div>
    <div><h3>OUR ADDRESS</h3><p>Suite 42, Level 3<br>8 Wattlebrook Lane<br>Fernvale Heights VIC 3999</p></div>
  </div>
  <div class="info" style="top:103px">
    <div class="icon"><svg width="17" height="17" viewBox="0 0 24 24"><path fill="#fff" d="M6.6 10.8a15 15 0 0 0 6.6 6.6l2.2-2.2c.3-.3.7-.4 1-.2 1.1.4 2.3.6 3.6.6.6 0 1 .4 1 1V20c0 .6-.4 1-1 1A17 17 0 0 1 3 4c0-.6.4-1 1-1h3.5c.6 0 1 .4 1 1 0 1.3.2 2.5.6 3.6.1.3 0 .7-.2 1z"/></svg></div>
    <div><h3>TELEPHONE</h3><p>1300 648 907</p></div>
  </div>
  <div class="info" style="top:177px">
    <div class="icon"><svg width="20" height="15" viewBox="0 0 20 15"><rect x="1" y="1" width="18" height="13" fill="none" stroke="#fff" stroke-width="1.8"/><path d="M1 1l9 7 9-7" fill="none" stroke="#fff" stroke-width="1.8"/></svg></div>
    <div><h3>EMAIL</h3><p>support@kavreo.example</p></div>
  </div>
</section>

<div class="map" role="img" aria-label="Grayscale street map marking the office location"></div>

<section class="tech-strip">
  <ul>
    <li><span class="sq"></span>Torvista</li>
    <li>QRX</li>
    <li>DataVane</li>
    <li>NCB</li>
  </ul>
</section>

<footer class="footer">
  <div class="col about">
    <h4>ABOUT US</h4>
    <p>Torvista, fully owned by Bayline Inc., is one of the most popular eCommerce platforms. It offers flexible, scalable eCommerce solutions designed to help businesses grow and succeed online. The Torvista platform is trusted by more than 150,000 businesses, including some of the world's leading brands.</p>
    <div class="badges">
      <div class="badge" role="img" aria-label="Torvista Certified Developer badge"></div>
      <div class="badge orange" role="img" aria-label="Torvista Certified Solution Provider badge"></div>
    </div>
  </div>
  <div class="col address-col">
    <h4>ADDRESS</h4>
    <p>Suite 42, Level 3, Larkmoor Building<br>8 Wattlebrook Lane<br>Fernvale Heights VIC 3999</p>
    <h4 class="sub">PHONE</h4>
    <div class="contact-line"><span class="dot"><svg width="9" height="9" viewBox="0 0 24 24"><path fill="#ccc" d="M6.6 10.8a15 15 0 0 0 6.6 6.6l2.2-2.2c.3-.3.7-.4 1-.2 1.1.4 2.3.6 3.6.6.6 0 1 .4 1 1V20c0 .6-.4 1-1 1A17 17 0 0 1 3 4c0-.6.4-1 1-1h3.5c.6 0 1 .4 1 1 0 1.3.2 2.5.6 3.6.1.3 0 .7-.2 1z"/></svg></span>1300 274 605</div>
    <h4 class="sub" style="margin-top:12px">EMAIL ID</h4>
    <div class="contact-line"><span class="dot"><svg width="9" height="7" viewBox="0 0 20 15"><rect x="1" y="1" width="18" height="13" fill="#ccc"/><path d="M1 1l9 7 9-7" fill="none" stroke="#555" stroke-width="2"/></svg></span>support@kavreo.example</div>
  </div>
  <div class="col news-col">
    <h4>NEWSLETTER SUBSCRIPTION</h4>
    <p>Subscribe to Torvista Support and Security Updates.</p>
    <div class="email">Email id</div>
    <div class="sub-btn">SUBSCRIBE</div>
  </div>
</footer>

<div class="bottombar">
  <nav><span>HOME</span><span>TORVISTA</span><span>PORTFOLIO</span><span>CONTACT</span></nav>
  <div class="copy">Copyright 2016 kavreo.example. All rights reserved</div>
</div>

</body>
</html>
```